International business needs business cards

Our company, DRV Ventures Inc. is in the business of supplying a range construction products with particular emphasis on CEMENT. We have developed our own brand - TORVAN SUPPLIES - with which to infiltrate the market. We are launching our brand of cement (TORVAN Type IS Cement) into the Caribbean which is unlike anything this market has ever seen. A monopoly has existed here for the past 60-odd years and the market has now opened to allow the importation of other brands and consumers are anxious and ready for change/improvement. We are very excited to be launching and want to make a great first impression. We will be conducting workshops and seminars (from government level to the hardware store owners) and we want our business card to give us the strong, confident introduction that we need.

Target Market(s)

construction; builders; engineers; home owners

Industry/Entity Type

Construction

Contact Information for Business Card

Marisol Depree
CEO
cell # 1 555 4180736
Ground floor,Lindell Plaza Suite 2734
George Town,Grand Cayman
Cayman Islands,KY1-4823
EMAIL: m.depree@drvventuresinc.example
web site drvventuresinc.example

COMPANY: skype info drv.ventures.example

second card
Yvette Brannock-Depree
CFO
CELL# 1 555 607 3941
George Town,Grand Cayman
Cayman Islands,KY1-4823
EMAIL: y.brannockdepree@drvventuresinc.example
website drvventuresinc.example

Requirements
Must have
• Business cards must display BOTH logos - DRV is the company and TORVAN is the brand.

```html
<!DOCTYPE html>
<html lang="en">
<head>
<meta charset="utf-8">
<title>DRV Ventures Inc. — Business Card</title>
<link href="https://fonts.googleapis.com/css2?family=Open+Sans:wght@400;600;700&display=swap" rel="stylesheet">
<style>
  :root {
    --backdrop: #9b9b9b;
    --card-white: #f4f4f3;
    --brand-red: #6b1216;
    --rule-red: #8b2a2a;
    --ink: #1b1b1b;
    --text-grey: #555555;
    --mark-grey: #4a4a4a;
    --white: #ffffff;
  }
  * { margin: 0; padding: 0; box-sizing: border-box; }
  html, body {
    width: 1105px;
    height: 1200px;
    overflow: hidden;
    background: var(--backdrop);
    font-family: "Open Sans", Arial, sans-serif;
  }
  .card {
    position: absolute;
    left: 180px;
    width: 746px;
    height: 427px;
  }
  .card--front { top: 119px; background: var(--card-white); }
  .card--back { top: 637px; background: var(--brand-red); }

  /* Company name block */
  .company {
    position: absolute;
    left: 29px;
    top: 44px;
    display: flex;
    align-items: flex-start;
    gap: 14px;
  }
  .company__square {
    width: 118px;
    height: 104px;
    background: var(--brand-red);
  }
  .company__name {
    color: var(--ink);
    font-weight: 700;
    line-height: 1;
  }
  .company__name-main { display: block; font-size: 72px; letter-spacing: -1px; }
  .company__name-sub { display: block; font-size: 20px; margin-top: 8px; letter-spacing: 0.5px; }

  /* Brand name block (front) */
  .brand {
    position: absolute;
    right: 38px;
    top: 30px;
    width: 150px;
    text-align: center;
  }
  .brand__circle {
    width: 100px;
    height: 100px;
    margin: 0 auto;
    border-radius: 50%;
    background: var(--mark-grey);
  }
  .brand__name {
    margin-top: 10px;
    font-size: 20px;
    font-weight: 700;
    letter-spacing: 3px;
    color: var(--mark-grey);
  }

  /* Person */
  .person__name {
    position: absolute;
    right: 28px;
    top: 228px;
    font-size: 25px;
    font-weight: 600;
    color: var(--brand-red);
  }
  .person__title {
    position: absolute;
    right: 28px;
    top: 264px;
    font-size: 18px;
    color: var(--ink);
  }
  .accent-bar {
    position: absolute;
    right: 0;
    top: 233px;
    width: 11px;
    height: 52px;
    background: var(--brand-red);
  }
  .divider {
    position: absolute;
    left: 29px;
    top: 280px;
    width: 645px;
    height: 1.5px;
    background: var(--rule-red);
  }

  /* Details */
  .address, .contact {
    position: absolute;
    top: 297px;
    font-size: 19px;
    line-height: 27.5px;
    color: var(--text-grey);
    font-style: normal;
  }
  .address { left: 29px; }
  .contact { right: 28px; text-align: right; }
  .contact__label { font-weight: 700; color: var(--brand-red); }

  /* Back */
  .brand--back {
    position: absolute;
    left: 50%;
    top: 100px;
    transform: translateX(-50%);
    text-align: center;
  }
  .brand--back .brand__circle {
    width: 150px;
    height: 150px;
    background: var(--white);
  }
  .brand--back .brand__name {
    color: var(--white);
    font-size: 26px;
    margin-top: 14px;
    letter-spacing: 5px;
  }
  .back__url {
    position: absolute;
    left: 0;
    right: 0;
    top: 375px;
    text-align: center;
    font-size: 18px;
    color: var(--white);
  }
</style>
</head>
<body>
  <section class="card card--front">
    <div class="company">
      <div class="company__square"></div>
      <div class="company__name">
        <span class="company__name-main">DRV</span>
        <span class="company__name-sub">VENTURES INC.</span>
      </div>
    </div>

    <div class="brand">
      <div class="brand__circle"></div>
      <div class="brand__name">TORVAN</div>
    </div>

    <div class="person__name">Marisol Depree</div>
    <div class="accent-bar"></div>
    <div class="divider"></div>
    <div class="person__title">CEO</div>

    <address class="address">
      Ground floor<br>
      Lindell Plaza Suite 2734<br>
      George Town,Grand Cayman<br>
      Cayman Islands,KY1-4823
    </address>

    <div class="contact">
      <span class="contact__label">Mobile:</span>1 555 4180736<br>
      m.depree@drvventuresinc.example<br>
      www.drvventuresinc.example
    </div>
  </section>

  <section class="card card--back">
    <div class="brand brand--back">
      <div class="brand__circle"></div>
      <div class="brand__name">TORVAN</div>
    </div>
    <div class="back__url">www.drvventuresinc.example</div>
  </section>
</body>
</html>
```